Business Card For Halvenmoor Financial Consulting

Hi, I would like a business card designed. Bold, modern.
Please use the same design as the logo. I have also attached the website design to see the overall theme.
Wordmark Font
Color: Hex: #01AEF7

```html
<!DOCTYPE html>
<html lang="en">
<head>
<meta charset="utf-8">
<title>Halvenmoor Financial Consulting – Business Card</title>
<link rel="stylesheet" href="https://fonts.googleapis.com/css2?family=Open+Sans:wght@400;600;700&display=swap">
<style>
  :root {
    --brand-blue: #35a8e0;
    --brand-navy: #0d3f63;
    --ink: #1c1c1c;
    --paper: #ffffff;
    --backdrop: #2a2b2e;
  }
  * { box-sizing: border-box; margin: 0; padding: 0; }
  html, body { width: 1200px; height: 780px; overflow: hidden; }
  body {
    background: var(--backdrop);
    font-family: "Open Sans", Arial, sans-serif;
    display: flex;
    flex-direction: column;
    align-items: center;
    justify-content: center;
    gap: 40px;
  }
  .card {
    position: relative;
    width: 600px;
    height: 343px;
    border-radius: 22px;
    overflow: hidden;
    background: var(--paper);
  }
  .card-swoosh { position: absolute; inset: 0; width: 100%; height: 100%; }
  .front-identity {
    position: absolute;
    left: 50%;
    top: 50%;
    transform: translate(-50%, -50%);
    display: flex;
    align-items: center;
    gap: 18px;
  }
  .identity-square {
    width: 54px;
    height: 54px;
    border: 6px solid var(--brand-blue);
    flex: none;
  }
  .identity-name {
    font-weight: 700;
    color: var(--brand-navy);
    font-size: 30px;
    line-height: 1.12;
    letter-spacing: 0.5px;
  }
  .back-name {
    position: absolute;
    left: 70px;
    top: 50%;
    transform: translateY(-50%);
    width: 200px;
    font-weight: 700;
    color: var(--brand-blue);
    font-size: 30px;
    line-height: 1.15;
  }
  .back-divider {
    position: absolute;
    left: 298px;
    top: 70px;
    width: 1px;
    height: 200px;
    background: var(--ink);
  }
  .contact-block {
    position: absolute;
    left: 320px;
    top: 62px;
    color: var(--ink);
    font-size: 12.5px;
    line-height: 1.4;
  }
  .person-name { color: var(--brand-blue); font-weight: 700; font-size: 23px; line-height: 1.1; }
  .person-role { font-size: 14px; margin-bottom: 12px; }
  .address { margin-bottom: 12px; }
  .contact-line { display: flex; align-items: center; gap: 7px; margin-bottom: 3px; }
  .contact-icon { width: 14px; height: 14px; flex: none; }
</style>
</head>
<body>

  <section class="card card-front" aria-label="Business card front">
    <svg class="card-swoosh" viewBox="0 0 600 343" aria-hidden="true">
      <rect width="600" height="343" fill="var(--brand-blue)"/>
      <ellipse cx="300" cy="175" rx="320" ry="210" transform="rotate(-14 300 175)" fill="var(--paper)"/>
    </svg>
    <div class="front-identity">
      <span class="identity-square"></span>
      <span class="identity-name">Halvenmoor<br>Financial Consulting</span>
    </div>
  </section>

  <section class="card card-back" aria-label="Business card back">
    <svg class="card-swoosh" viewBox="0 0 600 343" aria-hidden="true">
      <rect width="600" height="343" fill="var(--brand-blue)"/>
      <ellipse cx="300" cy="165" rx="325" ry="215" transform="rotate(-16 300 165)" fill="var(--paper)"/>
    </svg>

    <div class="back-name">Halvenmoor Financial Consulting</div>
    <div class="back-divider"></div>

    <div class="contact-block">
      <p class="person-name">Lenka Marovic</p>
      <p class="person-role">Managing Director</p>
      <p class="address">418 Alder Crest Blvd. Suite 210<br>Brookhaven, TX 75219</p>
      <p class="contact-line">
        <svg class="contact-icon" viewBox="0 0 16 16" aria-hidden="true"><path fill="var(--brand-blue)" d="M3.6 1.5l2.2 2.6-1.3 1.6a9 9 0 0 0 5.8 5.8l1.6-1.3 2.6 2.2-1.4 2.1C6.9 14.2 1.8 9.1 1.5 2.9z"/></svg>
        (555) 014-2290
      </p>
      <p class="contact-line">
        <svg class="contact-icon" viewBox="0 0 16 16" aria-hidden="true"><rect x="1" y="3" width="14" height="10" rx="1.5" fill="var(--brand-blue)"/><path d="M1.8 4l6.2 5 6.2-5" fill="none" stroke="#fff" stroke-width="1.4"/></svg>
        info@halvenmoor.com
      </p>
      <p class="contact-line">
        <svg class="contact-icon" viewBox="0 0 16 16" aria-hidden="true"><circle cx="8" cy="8" r="7" fill="var(--brand-blue)"/><path d="M1 8h14M8 1c-3 3.5-3 10.5 0 14M8 1c3 3.5 3 10.5 0 14" fill="none" stroke="#fff" stroke-width="1"/></svg>
        www.halvenmoor.com
      </p>
    </div>
  </section>

</body>
</html>
```